New Business Card Design Project

Use the flyer uploaded and website www.brightoakbuilders.com for inspiration.
List Our Services on Backside of business cards
Marcus Delling
Harborline Builders Inc.
Licensed General Contractors
858-471-6093

Contact Information for Business Card

Use the flyer uploaded and website www.brightoakbuilders.com for inspiration. List Our Services on Backside of business cards Marcus Delling Harborline Builders Inc. Licensed General Contractors 858-471-6093

```html
<!DOCTYPE html>
<html lang="en">
<head>
<meta charset="utf-8">
<title>Harborline Builders – Business Card</title>
<link rel="stylesheet" href="https://fonts.googleapis.com/css2?family=Roboto:wght@400;500;700;900&display=swap">
<style>
  :root {
    --stage: #2a2a2a;
    --card: #ffffff;
    --red: #ec1c24;
    --blue: #5282c6;
    --ink: #1a1a1a;
  }
  * { margin: 0; padding: 0; box-sizing: border-box; }
  html, body { width: 1200px; height: 780px; overflow: hidden; }
  body { background: var(--stage); font-family: "Roboto", Arial, sans-serif; color: var(--ink); position: relative; }

  .card {
    position: absolute; left: 328px; width: 545px; height: 311px;
    background: var(--card); border-radius: 24px; overflow: hidden;
    border: 2px solid var(--red);
  }
  .card--back { top: 63px; }
  .card--front { top: 406px; }

  .brand {
    position: absolute; display: flex; align-items: center; gap: 8px;
    font-size: 19px; font-weight: 500; letter-spacing: 1.5px; text-transform: uppercase; color: var(--ink);
  }
  .brand__mark { width: 12px; height: 12px; background: var(--ink); }
  .card--back .brand { left: 30px; top: 134px; }
  .card--front .brand { left: 14px; top: 178px; font-size: 17px; }

  .services { position: absolute; left: 336px; top: 50px; }
  .services__heading { font-size: 14px; font-weight: 700; line-height: 16px; color: var(--red); }
  .services__sub { font-size: 14px; font-weight: 700; line-height: 18px; color: var(--blue); margin-top: 1px; }
  .services__list { list-style: none; margin-top: 9px; }
  .services__item { display: flex; align-items: center; gap: 9px; font-size: 11.6px; height: 17.2px; letter-spacing: 0.2px; }
  .services__tick { width: 14px; height: 14px; flex: none; }

  .divider { position: absolute; left: 270px; top: 55px; width: 2px; height: 200px; background: var(--red); }

  .contact { position: absolute; left: 320px; top: 72px; }
  .contact__name { font-size: 31px; font-weight: 700; color: var(--red); line-height: 34px; }
  .contact__title { font-size: 12.3px; font-weight: 500; margin-top: 0; }
  .contact__company { font-size: 12.3px; margin-top: 25px; }
  .contact__list { list-style: none; margin-top: 14px; }
  .contact__row { display: flex; align-items: center; gap: 8px; font-size: 12.3px; height: 18.6px; }
  .contact__icon { width: 13px; height: 13px; flex: none; }

  .bands { position: absolute; left: 0; top: 270px; width: 545px; height: 20px; }
</style>
</head>
<body>

<section class="card card--back" aria-label="Card back: services">
  <div class="brand"><span class="brand__mark"></span>Harborline Builders</div>

  <div class="services">
    <p class="services__heading">OUR SERVICES ARE<br>100% GUARANTEED</p>
    <p class="services__sub">SPECIALIZING IN:</p>
    <ul class="services__list">
      <li class="services__item"><svg class="services__tick" viewBox="0 0 14 14"><circle cx="7" cy="7" r="5.8" fill="none" stroke="#ec1c24" stroke-width="1.2"/><path d="M4 7l2.2 2.3L12.5 2" fill="none" stroke="#ec1c24" stroke-width="1.5"/></svg>Remodel: Kitchen &amp; Bath</li>
      <li class="services__item"><svg class="services__tick" viewBox="0 0 14 14"><circle cx="7" cy="7" r="5.8" fill="none" stroke="#ec1c24" stroke-width="1.2"/><path d="M4 7l2.2 2.3L12.5 2" fill="none" stroke="#ec1c24" stroke-width="1.5"/></svg>Painting: Interior &amp; Exterior</li>
      <li class="services__item"><svg class="services__tick" viewBox="0 0 14 14"><circle cx="7" cy="7" r="5.8" fill="none" stroke="#ec1c24" stroke-width="1.2"/><path d="M4 7l2.2 2.3L12.5 2" fill="none" stroke="#ec1c24" stroke-width="1.5"/></svg>Flooring: Carpet, Vinyl, Wood</li>
      <li class="services__item"><svg class="services__tick" viewBox="0 0 14 14"><circle cx="7" cy="7" r="5.8" fill="none" stroke="#ec1c24" stroke-width="1.2"/><path d="M4 7l2.2 2.3L12.5 2" fill="none" stroke="#ec1c24" stroke-width="1.5"/></svg>Window &amp; Door Replacement</li>
      <li class="services__item"><svg class="services__tick" viewBox="0 0 14 14"><circle cx="7" cy="7" r="5.8" fill="none" stroke="#ec1c24" stroke-width="1.2"/><path d="M4 7l2.2 2.3L12.5 2" fill="none" stroke="#ec1c24" stroke-width="1.5"/></svg>Plumbing: Repairs &amp; Upgrades</li>
      <li class="services__item"><svg class="services__tick" viewBox="0 0 14 14"><circle cx="7" cy="7" r="5.8" fill="none" stroke="#ec1c24" stroke-width="1.2"/><path d="M4 7l2.2 2.3L12.5 2" fill="none" stroke="#ec1c24" stroke-width="1.5"/></svg>Energy-Efficient Upgrades</li>
      <li class="services__item"><svg class="services__tick" viewBox="0 0 14 14"><circle cx="7" cy="7" r="5.8" fill="none" stroke="#ec1c24" stroke-width="1.2"/><path d="M4 7l2.2 2.3L12.5 2" fill="none" stroke="#ec1c24" stroke-width="1.5"/></svg>Deck &amp; Patio Construction</li>
      <li class="services__item"><svg class="services__tick" viewBox="0 0 14 14"><circle cx="7" cy="7" r="5.8" fill="none" stroke="#ec1c24" stroke-width="1.2"/><path d="M4 7l2.2 2.3L12.5 2" fill="none" stroke="#ec1c24" stroke-width="1.5"/></svg>Water &amp; Mold Damage</li>
      <li class="services__item"><svg class="services__tick" viewBox="0 0 14 14"><circle cx="7" cy="7" r="5.8" fill="none" stroke="#ec1c24" stroke-width="1.2"/><path d="M4 7l2.2 2.3L12.5 2" fill="none" stroke="#ec1c24" stroke-width="1.5"/></svg>Garage Renovation</li>
    </ul>
  </div>
</section>

<section class="card card--front" aria-label="Card front: contact">
  <div class="brand"><span class="brand__mark"></span>Harborline Builders</div>

  <div class="divider"></div>

  <div class="contact">
    <h1 class="contact__name">Marcus Delling</h1>
    <p class="contact__title">Licensed General Contractors</p>
    <p class="contact__company">Harborline Builders Inc.</p>
    <ul class="contact__list">
      <li class="contact__row"><svg class="contact__icon" viewBox="0 0 14 14"><path d="M3 1.5l2 2.5-1.2 1.6c.8 1.8 2.2 3.2 4 4L9.4 8.4l2.6 2-1.2 2.2C6 12.3 1.7 8 1.4 3z" fill="#ec1c24"/></svg>858-471-6093</li>
      <li class="contact__row"><svg class="contact__icon" viewBox="0 0 14 14"><rect x="1" y="3" width="12" height="9" rx="1" fill="#ec1c24"/><path d="M1.5 3.5L7 8l5.5-4.5" fill="none" stroke="#fff" stroke-width="1.1"/></svg>info@brightoakbuilders.com</li>
      <li class="contact__row"><svg class="contact__icon" viewBox="0 0 14 14"><circle cx="7" cy="7" r="6" fill="#ec1c24"/><ellipse cx="7" cy="7" rx="2.5" ry="6" fill="none" stroke="#fff" stroke-width="0.9"/><path d="M1 7h12" stroke="#fff" stroke-width="0.9"/></svg>www.brightoakbuilders.com</li>
    </ul>
  </div>

  <svg class="bands" viewBox="0 0 545 20" preserveAspectRatio="none">
    <path d="M0 0H238Q246 0 252 4L277 20H0Z" fill="#ec1c24"/>
    <path d="M263 0H545V20H302Q294 20 288 16Z" fill="#5282c6"/>
  </svg>
</section>

</body>
</html>
```